Website design and coding for new consultancy company

I need to have a full website designed for a new consultancy business I'm trying to establish. It's called BrightPath consult. I need an English version to begin with, and then there should be a Danish version as well, but I'll translate that myself. Just be aware that I need two language versions. The consultancy field that I'm targeting is Leadership - and specialist development. I offer to facilitate corporate academies for global companies as well as specific workshops within leadership- or team development, strategy sessions, personal coaching and facilitation of D&I (Diversity and inclusion) workshops. BTW my logo is not in high resolution - I need that as well.

Target Market(s)

Larger companies that has a need for developing their inhouse leadership capabilities or that wants to develop their specialists to take on more responsibility.

Industry/Entity Type

Consultancy business

Coding

Coded - Design and coding required

Number of Pages Required

5+ page

Requirements
Must have
• Introduction site with a catch phrase. Book a meeting. Services that's beeing offered. Blog site with white papers etc. Language toggle (Danish/English). Cases/testimonials. About site. Contact site.

```html
<!DOCTYPE html>
<html lang="en">
<head>
<meta charset="utf-8">
<title>BrightPath consult – Leadership Development</title>
<link href="https://fonts.googleapis.com/css2?family=Montserrat:ital,wght@0,500;0,600;0,700;1,700&family=Lato:wght@400;700&display=swap" rel="stylesheet">
<style>
:root{
  --blue:#2a84cc;
  --blue-dark:#1f6fb0;
  --ink:#111111;
  --text:#444444;
  --muted:#5a5a5a;
  --pale:#e3f1fc;
  --white:#ffffff;
  --line:#e2e2e2;
  --star:#f5b400;
}
*{margin:0;padding:0;box-sizing:border-box}
html,body{width:1200px;height:3687px;overflow:hidden}
body{position:relative;background:var(--white);font-family:'Lato',sans-serif;color:var(--text)}
.section{position:absolute;left:0;width:1200px}
.abs{position:absolute}
.heading{font-family:'Montserrat',sans-serif;font-weight:500;color:var(--ink);font-size:40px;text-align:center;width:100%}
.heading b{color:var(--blue);font-weight:700}
.rule{position:absolute;height:3px;width:94px;background:var(--ink);left:553px}
.btn{position:absolute;background:var(--blue);color:var(--white);font-family:'Lato',sans-serif;font-weight:700;font-size:16px;display:flex;align-items:center;justify-content:center}

/* header */
.site-header{top:0;height:86px;background:var(--white)}
.brand{left:110px;top:20px;font-family:'Montserrat',sans-serif;font-weight:700;font-size:38px;color:var(--ink);display:flex;align-items:center;gap:12px;letter-spacing:-0.5px}
.brand i{display:block;width:14px;height:14px;border-radius:50%;background:var(--blue)}
.nav{top:32px;left:498px;display:flex;gap:28px;font-size:14.5px;color:var(--ink)}
.nav .active{color:var(--blue);text-decoration:underline}
.lang{left:850px;top:31px;display:flex;align-items:center;gap:10px;font-size:14.5px;color:var(--ink)}
.flag{width:32px;height:20px;background:linear-gradient(#c8102e,#c8102e) center/100% 5px no-repeat,linear-gradient(#c8102e,#c8102e) center/5px 100% no-repeat,#27408b}
.caret{width:0;height:0;border-left:5px solid transparent;border-right:5px solid transparent;border-top:6px solid var(--ink)}

/* hero */
.hero{top:86px;height:513px;background:linear-gradient(90deg,#222a33 0%,#2e3740 35%,#5d6a73 60%,#8d979c 80%,#6b7479 100%)}
.hero-title{left:87px;top:98px;font-family:'Montserrat',sans-serif;font-weight:700;font-size:53px;line-height:60px}
.hero-title .l1{color:var(--blue)}
.hero-title .l2{color:var(--white);font-style:italic}
.hero-sub{left:91px;top:243px;width:520px;color:var(--white);font-weight:700;font-size:17px;line-height:26px}

/* services */
.services{top:599px;height:604px}
.card{position:absolute;background:var(--white);border:1px solid var(--line);box-shadow:0 2px 6px rgba(0,0,0,.12)}
.svc-card{top:165px;width:305px;height:351px}
.svc-img{position:absolute;left:10px;top:10px;width:285px;height:289px}
.svc-title{position:absolute;left:0;width:100%;top:312px;text-align:center;font-family:'Montserrat',sans-serif;font-weight:500;font-size:22px;color:var(--ink)}
.arrow{position:absolute;width:22px;height:22px;border-radius:50%;background:var(--blue);display:flex;align-items:center;justify-content:center}
.arrow.light{background:#9cc8ea}

/* about */
.about{top:1203px;height:645px;background:var(--pale)}
.about h2{position:absolute;left:108px;top:92px;font-family:'Montserrat',sans-serif;font-weight:500;font-size:40px;color:var(--ink)}
.about h2 b{color:var(--blue);font-weight:700}
.about .rule{left:108px;top:138px;width:140px}
.about p{position:absolute;left:108px;top:177px;width:444px;font-size:14.8px;line-height:25.8px;text-align:justify;color:var(--text)}
.portrait-shadow{left:656px;top:94px;width:433px;height:468px;background:var(--blue)}
.portrait{left:645px;top:83px;width:435px;height:468px;background:linear-gradient(160deg,#d9dde0,#b9c2c8 55%,#2b3a52 100%);border:2px solid var(--white)}

/* why */
.why{top:1848px;height:634px}
.why-sub{top:152px;left:0;width:100%;text-align:center;font-size:14.5px;line-height:26px;color:var(--ink)}
.feature{position:absolute;width:380px;text-align:center}
.feature svg{display:block;margin:0 auto}
.feature h3{font-family:'Montserrat',sans-serif;font-weight:600;font-size:19px;color:var(--ink);margin-top:10px}
.feature p{font-size:14.5px;color:var(--muted);margin-top:12px}

/* cta */
.cta{top:2482px;height:386px;background:linear-gradient(180deg,#2f86cf,#2a7fc6)}
.cta h2{position:absolute;top:80px;width:100%;text-align:center;font-family:'Montserrat',sans-serif;font-weight:500;font-size:38px;color:var(--white)}
.cta h2 b{font-weight:700}
.cta .rule{background:var(--white);top:144px}
.cta p{position:absolute;top:175px;width:100%;text-align:center;color:var(--white);font-size:15px;line-height:26px}
.cta .btn{left:533px;top:256px;width:134px;height:45px;background:var(--white);color:var(--ink);font-size:15px}

/* testimonials */
.testimonials{top:2868px;height:483px}
.t-card{top:168px;width:305px;height:230px}
.avatar{position:absolute;left:20px;top:33px;width:78px;height:78px;border-radius:50%;background:linear-gradient(160deg,#d7e3ea,#a9bcc8)}
.t-name{position:absolute;left:118px;top:54px;font-weight:700;font-size:16px;color:var(--ink)}
.t-role{position:absolute;left:118px;top:78px;font-size:12.5px;color:var(--blue)}
.t-stars{position:absolute;left:118px;top:96px;color:var(--star);font-size:12px;letter-spacing:1px}
.quote{position:absolute;right:20px;top:20px;font-family:'Montserrat',sans-serif;font-weight:700;font-size:34px;line-height:34px;color:#9cc8ea}
.t-text{position:absolute;left:22px;top:126px;width:263px;font-size:12.5px;line-height:20px;color:var(--muted);text-align:justify}

/* footer */
.footer{top:3351px;height:336px;background:var(--blue)}
.footer .brand{left:0;width:100%;top:90px;justify-content:center;color:var(--white);font-size:54px}
.footer .brand i{background:var(--white);width:20px;height:20px}
.foot-nav{top:211px;width:100%;display:flex;justify-content:center;gap:15px;color:var(--white);font-size:15px}
.social{top:255px;width:100%;display:flex;justify-content:center;gap:16px}
.social span{width:20px;height:20px;border-radius:50%;background:var(--white)}
.foot-line{left:111px;top:299px;width:978px;height:1px;background:rgba(255,255,255,.45)}
.copy{top:310px;width:100%;text-align:center;color:var(--white);font-size:15px}
</style>
</head>
<body>

<header class="section site-header">
  <div class="abs brand"><i></i>BRIGHTPATH</div>
  <nav class="abs nav"><span class="active">Home</span><span>About</span><span>Services</span><span>Clients &amp; Impact</span></nav>
  <div class="abs lang"><span class="flag"></span>EN<span class="caret"></span></div>
  <a class="btn" style="left:954px;top:20px;width:134px;height:46px">Contact Us</a>
</header>

<section class="section hero" role="img" aria-label="Team of colleagues collaborating around a laptop in a bright modern office">
  <h1 class="abs hero-title"><span class="l1">Empowering Leaders</span><br><span class="l2">Enabling Growth</span></h1>
  <p class="abs hero-sub">We help organizations and individuals unlock potential through leadership development, strategy facilitation, and coaching.</p>
  <a class="btn" style="left:91px;top:323px;width:134px;height:47px">Get Started</a>
</section>

<section class="section services">
  <h2 class="abs heading" style="top:75px">Our <b>Services</b></h2>
  <div class="rule" style="top:130px"></div>
  <span class="arrow" style="left:46px;top:312px"><svg width="10" height="10" viewBox="0 0 10 10"><path d="M6.5 1.5 3 5l3.5 3.5" fill="none" stroke="#fff" stroke-width="2"/></svg></span>
  <span class="arrow light" style="left:1128px;top:312px"><svg width="10" height="10" viewBox="0 0 10 10"><path d="M3.5 1.5 7 5 3.5 8.5" fill="none" stroke="#fff" stroke-width="2"/></svg></span>
  <div class="card svc-card" style="left:111px">
    <div class="svc-img" role="img" aria-label="Presenter speaking to a seated audience in front of a chart screen" style="background:linear-gradient(160deg,#6d8fa6,#2f3e4a 70%,#1d2328)"></div>
    <div class="svc-title">Corporate Academies</div>
  </div>
  <div class="card svc-card" style="left:448px">
    <div class="svc-img" role="img" aria-label="Smiling workshop participants next to a wall of colourful sticky notes" style="background:linear-gradient(110deg,#8a8275,#b9a58f 50%,#6fa9c8 80%,#e0b23c)"></div>
    <div class="svc-title">Strategy Sessions</div>
  </div>
  <div class="card svc-card" style="left:784px">
    <div class="svc-img" role="img" aria-label="Coaching conversation at a table by a large window" style="background:linear-gradient(120deg,#4d5a57,#a7b3ac 45%,#e7e6e2 75%,#c9c3bb)"></div>
    <div class="svc-title">Coaching</div>
  </div>
</section>

<section class="section about">
  <h2>About <b>Me</b></h2>
  <div class="rule"></div>
  <p>BrightPath Consult is dedicated to developing leaders, specialists, and organizations to thrive in today's complex, fast-changing world. We believe that leadership is not about titles — it's about practice, awareness, and the ability to bring out the best in others. That's why we design and facilitate programs that go beyond theory, creating practical learning experiences that drive real change. With expertise in leadership development, corporate academies, strategy facilitation, coaching, and diversity &amp; inclusion, we work with global companies to strengthen their talent and unlock potential at every level.</p>
  <a class="btn" style="left:108px;top:476px;width:142px;height:47px">Read More</a>
  <div class="abs portrait-shadow"></div>
  <div class="abs portrait" role="img" aria-label="Portrait of the consultant in a navy blazer"></div>
</section>

<section class="section why">
  <h2 class="abs heading" style="top:75px">Why <b>Choose Us</b></h2>
  <div class="rule" style="top:130px"></div>
  <p class="abs why-sub">At BrightPath Consult, we combine global experience with a human-centered approach<br>to create lasting impact. Here's what sets us apart</p>

  <div class="feature" style="left:178px;top:230px">
    <svg width="64" height="76" viewBox="0 0 64 76"><circle cx="38" cy="26" r="14" fill="#2a84cc"/><rect x="33" y="40" width="10" height="8" fill="#2a84cc"/><path d="M4 62h14l12 6h18l10-8" fill="none" stroke="#2a84cc" stroke-width="6" stroke-linecap="round"/><path d="M38 4v-4M56 12l4-3M20 12l-4-3M60 26h4M12 26h4" stroke="#2a84cc" stroke-width="3"/></svg>
    <h3>Tailored Solutions</h3>
    <p>We design programs and workshops that fit your</p>
  </div>
  <div class="feature" style="left:670px;top:230px">
    <svg width="76" height="76" viewBox="0 0 76 76"><circle cx="38" cy="30" r="20" fill="none" stroke="#2a84cc" stroke-width="5"/><path d="M18 30h40M38 10v40" stroke="#2a84cc" stroke-width="3"/><circle cx="10" cy="56" r="6" fill="#2a84cc"/><circle cx="38" cy="66" r="6" fill="#2a84cc"/><circle cx="66" cy="56" r="6" fill="#2a84cc"/></svg>
    <h3>Global Perspective</h3>
    <p>Experience working with international teams and</p>
  </div>
  <div class="feature" style="left:94px;top:410px">
    <svg width="64" height="60" viewBox="0 0 64 60"><rect x="6" y="2" width="40" height="28" fill="none" stroke="#2a84cc" stroke-width="4"/><path d="M14 12h24M14 20h16" stroke="#2a84cc" stroke-width="3"/><circle cx="54" cy="30" r="6" fill="#2a84cc"/><circle cx="10" cy="46" r="5" fill="#2a84cc"/><circle cx="24" cy="46" r="5" fill="#2a84cc"/><circle cx="38" cy="46" r="5" fill="#2a84cc"/><path d="M4 58h40" stroke="#2a84cc" stroke-width="5"/></svg>
    <h3>Engaging Facilitation</h3>
    <p>Experience working with international teams and</p>
  </div>
  <div class="feature" style="left:713px;top:410px">
    <svg width="60" height="60" viewBox="0 0 60 60"><circle cx="30" cy="26" r="8" fill="#2a84cc"/><path d="M16 58v-12a14 10 0 0 1 28 0v12z" fill="#2a84cc"/><path d="M30 2l2 4 4 .5-3 3 1 4-4-2-4 2 1-4-3-3 4-.5z" fill="#2a84cc"/><path d="M8 12l2 3 3 .5-2 2 .5 3-3.5-1.5-3.5 1.5.5-3-2-2 3-.5z" fill="#2a84cc"/><path d="M52 12l2 3 3 .5-2 2 .5 3-3.5-1.5-3.5 1.5.5-3-2-2 3-.5z" fill="#2a84cc"/></svg>
    <h3>Proven Expertise</h3>
    <p>Deep knowledge in leadership, strategy, coaching, and</p>
  </div>
</section>

<section class="section cta">
  <h2>Ready to strengthen <b>your leadership?</b></h2>
  <div class="rule"></div>
  <p>Whether you're building a corporate academy, aligning your leadership team, or looking for personal<br>coaching, we'd love to hear from you.</p>
  <a class="btn">Contact Us</a>
</section>

<section class="section testimonials">
  <h2 class="abs heading" style="top:75px">What People <b>Are Saying</b></h2>
  <div class="rule" style="top:130px"></div>
  <span class="arrow" style="left:44px;top:283px"><svg width="10" height="10" viewBox="0 0 10 10"><path d="M6.5 1.5 3 5l3.5 3.5" fill="none" stroke="#fff" stroke-width="2"/></svg></span>
  <span class="arrow light" style="left:1134px;top:283px"><svg width="10" height="10" viewBox="0 0 10 10"><path d="M3.5 1.5 7 5 3.5 8.5" fill="none" stroke="#fff" stroke-width="2"/></svg></span>

  <div class="card t-card" style="left:111px">
    <div class="avatar" role="img" aria-label="Client portrait"></div>
    <div class="quote">”</div>
    <div class="t-name">Dr. Hanna Lind</div>
    <div class="t-role">Global Corporate Academy</div>
    <div class="t-stars">★★★★★</div>
    <p class="t-text">The academy designed and facilitated by BrightPath Consult had a real impact on our leadership culture. The sessions were engaging, practical, and directly applicable to</p>
  </div>
  <div class="card t-card" style="left:448px">
    <div class="avatar" role="img" aria-label="Client portrait"></div>
    <div class="quote">”</div>
    <div class="t-name">Tomas Berg</div>
    <div class="t-role">VP Strategy,</div>
    <div class="t-stars">★★★★★</div>
    <p class="t-text" style="text-align:left">Our leadership team walked away with new clarity and energy. The facilitation balanced structure with open dialogue, which helped us align on our strategy and next steps.</p>
  </div>
  <div class="card t-card" style="left:784px">
    <div class="avatar" role="img" aria-label="Client portrait"></div>
    <div class="quote">”</div>
    <div class="t-name">Prof. Clara Holm</div>
    <div class="t-role">Global Pharma Company</div>
    <div class="t-stars">★★★★★</div>
    <p class="t-text">The coaching experience has been transformative — both personally and professionally. The D&amp;I workshops also gave us tools to create a more inclusive</p>
  </div>
</section>

<footer class="section footer">
  <div class="abs brand"><i></i>BRIGHTPATH</div>
  <nav class="abs foot-nav"><span>Home</span><span>|</span><span>About</span><span>|</span><span>Services</span><span>|</span><span>Clients &amp; Impact</span><span>|</span><span>Contact Us</span></nav>
  <div class="abs social"><span></span><span></span><span></span><span></span></div>
  <div class="abs foot-line"></div>
  <div class="abs copy">© 2025 BrightPath consult. All rights reserved.</div>
</footer>

</body>
</html>
```